Webdesign für Industrieanlagenbau-Unternehmen
Zielgruppe
Die KLR services GmbH ist ein ein österreichisches, eigentümergeführtes Industrieanlagenbau-Unternehmen mit Niederlassungen an derzeit 2 Standorten (Wiesenau/NÖ und Bergfeld/Sbg) und ist in den Geschäftsfeldern Industrieanlagenbau, Reinraumtechnik und Sondermaschinenbau - sowie im Projekt- und Behördenmanagement tätig.
Die KLR services GmbH unterstützt ihre B2B-Kunden bei der Umsetzung von Engineering-Projekten in der Hightech-, Elektronik- und Prozessindustrie.
Unsere Kernkompetenzen sind Konzepterstellung, 3D-Planung, Konstruktion, Design und Montage von Prozessanlagen und Reinräumen, eine eigene Fertigung und Prototypenbau in unserer „Werkhalle Quellbach“ sowie die Abwicklung des Behörden-Managements wie z.B. Einreichverfahren nach Gewerbeordnung.
Langjährige und dauerhafte Geschäftsbeziehungen zu unseren Kunden stehen bei uns im Vordergrund.
Zielsgruppe der neuen website:
„Visitenkarte“ der KLR services GmbH
potentielle Mitarbeiter („Employer Branding“), Ingenieure/Projektmanager (WI-Maschinenbau, Elektro- und Prozesstechnik), Mechatroniker, Schlosser, Elektriker
B2B Kunden aus Bereichen Mikroelektronik-Fertigung, chemische Industrie, Lebensmittel- und Pharmaproduktion
Bestandskunden (Stakeholder des „Buying Centers“ bei Kunden)
Neukunden „eingeschränkt“ (dzt. Keine aktive Kundenakquise via web geplant)
Aufgabenstellung
Allgemeine Anforderungen an die neue website:
Ziel sind eher „schlanke“ Texte & Design (vgl. https://www.varnhold-gruppe.com/de/)
Produkt- und Leistungsspezifisches Bildmaterial sollen hauptsächlich KLR-eigene Fotos und Videos sein (Stock-Fotos nur für Allgemeine Bilder). Beispielhaftes Bildmaterial (sollte durch KLR Mitarbeiter dann im CMS einfach ausgetauscht werden können) in diesen Unterlagen
CMS (Content Management System) zur Administration durch KLR Mitarbeiter
Hosting auf europäischen ServernServern (z.B. https://serverkiste-demo.com/, https://www.datenfeld-demo.com, https://www.rechenhof-demo.de, https://www.netzquelle-demo.com/, https://www.zuvo-demo.at)
Basierend auf weitverbreiteten open-Source Systemen (z.B. Wordpress , Joomla, TYPO3)
Responsive Webdesign – eine Website für alle Geräte (PC, Tablet, Smartphone) und alle gängigen Browser (Chrome, Edge, Safari, Firefox, Opera, Internet Explorer)
Google Pagespeed mind. 85 Punkte, GTmetrix Grade > 80%
Sicherheitszertifikat (SSL-Zertifikat)
Sprache – Deutsch, Englisch
E-Commerce-Gesetz (ECG) & DSGVO konform (Cookie Disclaimer Standard „nur notwendige“)
Impressum
AGB - Allgemeine Lieferungs- und Zahlungsbedingungen
Sitemap
Vollständige Rechte an der website (Design, Inhalt etc.) bei KLR services GmbH
Einbettung von Text, Fotos und Videos durch KLR Mitarbeiter
Hinzufügen von Menü-Unterpunkten durch KLR Mitarbeiter

```html
<!DOCTYPE html>
<html lang="de">
<head>
<meta charset="utf-8">
<title>Jobs/Karriere – KLR services GmbH</title>
<link rel="stylesheet" href="https://fonts.googleapis.com/css2?family=Open+Sans:wght@400;600;700&display=swap">
<style>
:root{
  --red:#e3241f;
  --text:#333;
  --page:#f4f4f4;
  --band:#ececec;
  --rule:#c4c4c4;
  --navy:#162a3d;
  --white:#fff;
}
*{box-sizing:border-box;margin:0;padding:0}
html,body{width:1200px;height:3175px;overflow:hidden}
body{position:relative;background:var(--page);font-family:"Open Sans",Arial,sans-serif;color:var(--text)}
.site-header{position:absolute;left:0;top:0;width:1200px;height:131px;background:#f7f7f7}
.brand{position:absolute;left:76px;top:38px;display:flex;align-items:center;gap:12px;color:var(--red);font-weight:700;font-size:46px;line-height:52px}
.brand-dot{width:36px;height:36px;background:var(--red);border-radius:4px}
.main-nav{position:absolute;top:54px;left:0;width:1200px;font-weight:600;font-size:18px;color:#333}
.main-nav a{position:absolute;color:inherit;text-decoration:none}
.main-nav a.active{color:var(--red)}
.hero{position:absolute;left:0;top:131px;width:1200px;height:319px;background:linear-gradient(100deg,#6b717a 0%,#4d5662 45%,#3d4655 100%)}
.hero h1{position:absolute;left:0;right:0;top:116px;text-align:center;color:var(--white);font-size:60px;font-weight:700;line-height:72px}
.jobs{position:absolute;left:75px;top:517px;width:784px}
.job{border-top:3px solid var(--rule)}
.job:last-child{border-bottom:3px solid var(--rule)}
.job-head{display:flex;justify-content:space-between;align-items:center;height:63px;padding:0 5px;color:var(--red);font-weight:700;font-size:25px}
.toggle{width:22px;height:22px}
.job-body{padding:2px 5px 50px 5px;font-size:16px;line-height:24.5px}
.job-body p{margin-bottom:19px;white-space:nowrap}
.job-body p.label{font-weight:700}
.job-body ul{list-style:none;margin-bottom:19px;white-space:nowrap}
.job-body li{position:relative;padding-left:24px}
.job-body li::before{content:"";position:absolute;left:9px;top:11px;width:4px;height:4px;border-radius:50%;background:#555}
.apply{display:inline-flex;align-items:center;justify-content:center;gap:18px;width:340px;height:54px;margin-top:6px;background:var(--red);color:var(--white);font-weight:700;font-size:24px;text-decoration:none}
.contact-card{position:absolute;left:898px;top:569px;width:200px;text-align:center;font-size:15px;line-height:22.5px}
.avatar{width:108px;height:108px;border-radius:50%;margin:0 auto 10px;background:linear-gradient(160deg,#b9bcc0,#7b8694 60%,#2f5ea8)}
.contact-card strong{font-weight:700}
.contact-card a{color:var(--text);text-decoration:underline}
.workplace{position:absolute;left:0;top:2251px;width:1200px;height:586px;background:var(--band)}
.workplace h2{position:absolute;left:78px;top:137px;color:var(--red);font-size:25px;font-weight:700}
.workplace .intro{position:absolute;left:78px;top:180px;width:460px;font-size:16px;line-height:24.5px;white-space:nowrap}
.perks{position:absolute;left:78px;top:264px;width:460px;list-style:none;font-size:16px;line-height:24.5px;white-space:nowrap}
.perks li{position:relative;padding-left:26px;margin-bottom:6px}
.perks svg{position:absolute;left:0;top:3px}
.team-photo{position:absolute;left:563px;top:91px;width:517px;height:404px;background:linear-gradient(135deg,#c7b08a 0%,#8b7a63 40%,#4f5662 75%,#2f5f9e 100%)}
.site-footer{position:absolute;left:0;top:2837px;width:1200px;height:338px;background:var(--navy);color:var(--white);font-size:14px;line-height:21.5px}
.foot-col{position:absolute;top:46px}
.foot-col h3{color:var(--red);font-size:16px;font-weight:700;margin-bottom:10px}
.foot-col a{display:block;color:var(--white);text-decoration:none}
.foot-brand{position:absolute;left:918px;top:50px;display:flex;align-items:center;gap:10px;font-weight:700;font-size:42px;line-height:48px}
.foot-brand-dot{width:36px;height:36px;border:3px solid var(--white);border-radius:4px}
.foot-address{position:absolute;left:924px;top:106px;font-size:12.5px;line-height:18.5px;font-weight:600}
.foot-address p{margin-bottom:18px}
.foot-address strong{font-weight:700}
.legal{position:absolute;left:75px;top:304px;font-size:11px;font-weight:600;color:#aab4bf}
.legal span,.legal a{position:absolute;white-space:nowrap;color:#aab4bf}
</style>
</head>
<body>
<header class="site-header">
  <div class="brand"><span class="brand-dot"></span>KLR</div>
  <nav class="main-nav">
    <a style="left:469px">Home</a>
    <a style="left:569px">Leistungen</a>
    <a class="active" style="left:715px">Jobs/Karriere</a>
    <a style="left:880px">Kontakt</a>
    <a style="left:998px">Kunden-Portal</a>
  </nav>
</header>

<section class="hero" role="img" aria-label="Foto: Techniker misst ein Bauteil mit einem Messschieber">
  <h1>Jobs/Karriere</h1>
</section>

<main class="jobs">
  <article class="job">
    <div class="job-head">Stellenanzeige Beispiel 1
      <svg class="toggle" viewBox="0 0 22 22"><rect x="0" y="9" width="22" height="4" fill="#e3241f"/><rect x="9" y="0" width="4" height="22" fill="#e3241f"/></svg>
    </div>
  </article>
  <article class="job">
    <div class="job-head">Techniker / Project Engineer / Elektrotechnik
      <svg class="toggle" viewBox="0 0 22 22"><rect x="2" y="0" width="18" height="4" fill="#e3241f"/></svg>
    </div>
    <div class="job-body">
      <p class="label">Dienstort: 2471 Wiesenau</p>
      <p>Die KLR services GmbH ist ein stabiles und eigentümergeführtes Unternehmen mit<br>Niederlassungen an derzeit 2 Standorten (Wiesenau/NÖ und Bergfeld/Sbg).</p>
      <p>Die KLR services GmbH ist in den Geschäftsfeldern Industrieanlagenbau, Reinraumtechnik<br>und Sondermaschinenbau - sowie im Projekt- und Behördenmanagement tätig.</p>
      <p>Unterstützen Sie uns bei der Umsetzung interessanter und abwechslungsreicher<br>Kundenprojekte im B2B-Segment. Zu unseren Kunden zählen namhafte Konzerne, unter<br>anderem Weltmarktführer in der Hightech-, Elektronik- und Prozessindustrie.</p>
      <p>Langjährige und dauerhafte Geschäftsbeziehungen zu unseren Kunden stehen bei uns im<br>Vordergrund.</p>
      <p class="label">Ihre Aufgaben:</p>
      <ul>
        <li>Selbständige Abwicklung von E/MSR-Planungsarbeiten in<br>multidisziplinären Projekten</li>
        <li>Planung und Auslegung von E/MSR Anlagen bzw. Komponenten<br>für Industrieanlagen und Reinraumapplikationen</li>
        <li>Entwicklung von Mess-, Regelungs- und Steuerungskonzepten<br>für Industrieanlagen und Reinraumapplikationen</li>
        <li>Abstimmung und Zusammenarbeit mit verschiedenen Gewerken<br>sowie mit Kunden und Lieferanten</li>
        <li>Softwareerstellung für Automation und Visualisierung, für speicher-<br>programmierbare Steuerungen (VALTRO, NORDLEK)</li>
      </ul>
      <p class="label">Ihr Profil:</p>
      <ul>
        <li>Abgeschlossene technische Ausbildung – Mindestanforderung HTL<br>Automatisierungstechnik, HTL-Elektrotechnik oder höhere Ausbildung (FH, TU)</li>
        <li>Einschlägige Berufserfahrung von mindestens 5 Jahren in der E/MSR-Projektierung<br>im Umfeld Industrieanlagenbau</li>
        <li>Sie arbeiten gerne selbstständig, abteilungsübergreifend und strukturiert</li>
        <li>Sie sind kreativ, geistig flexibel und haben „Hands-On“ Mentalität</li>
        <li>Sie verfügen über ein hohes Maß an Organisationsfähigkeit und Eigenverantwortung</li>
      </ul>
      <p class="label">Wir bieten:</p>
      <ul>
        <li>Genießen Sie die Vorzüge von flachen Hierarchien mit einem hohen Maß an<br>Eigenverantwortung und Entfaltungsmöglichkeiten für Ihre persönliche Kreativität</li>
        <li>Mitgestaltungsmöglichkeiten in einem rasant wachsenden Unternehmen</li>
        <li>Individuelle Karriere- und Entwicklungsmöglichkeiten</li>
        <li>Ggf. Dienstwagen auch zur privaten Nutzung – wird bei<br>Gehaltsverhandlungen festgelegt</li>
        <li>Gleitzeitregelung</li>
        <li>Firmenparkplatz</li>
        <li>Laptop und Mobiltelefon auch zur privaten Nutzung</li>
      </ul>
      <p>Die Entlohnung erfolgt nach dem gültigen Kollektivvertrag Metallgewerbe. Abhängig<br>von Ihrer Qualifikation und Berufserfahrung ist für die ausgeschriebene Position, ein<br>Brutto-Jahresgehalt ab/von EUR 50.000,00 vorgesehen.</p>
      <p>Das tatsächliche Gehalt mit der Möglichkeit einer Überzahlung wird mit Ihnen<br>gemeinsam festgelegt und ist abhängig von Qualifikation und Erfahrung.</p>
      <a class="apply">Jetzt bewerben
        <svg width="14" height="24" viewBox="0 0 14 24"><path d="M2 2l10 10L2 22" fill="none" stroke="#fff" stroke-width="3"/></svg>
      </a>
    </div>
  </article>
  <article class="job">
    <div class="job-head">Stellenanzeige Beispiel 2
      <svg class="toggle" viewBox="0 0 22 22"><rect x="0" y="9" width="22" height="4" fill="#e3241f"/><rect x="9" y="0" width="4" height="22" fill="#e3241f"/></svg>
    </div>
  </article>
</main>

<aside class="contact-card">
  <div class="avatar" role="img" aria-label="Porträtfoto des Ansprechpartners"></div>
  <p>Sie haben Fragen?</p>
  <p><strong>DI Lukas Vernhofer, MBA</strong></p>
  <p>+43 (0) 555018-12</p>
  <p><a>hr@klr-service.example</a></p>
</aside>

<section class="workplace">
  <h2>Arbeiten bei KLR</h2>
  <p class="intro">Genießen Sie die Vorzüge von flachen Hierarchien<br>mit einem hohen Maß an Eigenverantwortung und<br>Entfaltungsmöglichkeiten für Ihre persönliche Kreativität.</p>
  <ul class="perks">
    <li><svg width="18" height="18" viewBox="0 0 18 18"><path d="M1 9l5 6L17 1" fill="none" stroke="#e3241f" stroke-width="3.5"/></svg>Mitgestaltungsmöglichkeiten in einem rasant<br>wachsenden Unternehmen</li>
    <li><svg width="18" height="18" viewBox="0 0 18 18"><path d="M1 9l5 6L17 1" fill="none" stroke="#e3241f" stroke-width="3.5"/></svg>Individuelle Karriere- und Entwicklungsmöglichkeiten</li>
    <li><svg width="18" height="18" viewBox="0 0 18 18"><path d="M1 9l5 6L17 1" fill="none" stroke="#e3241f" stroke-width="3.5"/></svg>Gleitzeitregelung</li>
    <li><svg width="18" height="18" viewBox="0 0 18 18"><path d="M1 9l5 6L17 1" fill="none" stroke="#e3241f" stroke-width="3.5"/></svg>Firmenparkplatz</li>
    <li><svg width="18" height="18" viewBox="0 0 18 18"><path d="M1 9l5 6L17 1" fill="none" stroke="#e3241f" stroke-width="3.5"/></svg>Laptop und Mobiltelefon auch zur privaten Nutzung</li>
  </ul>
  <div class="team-photo" role="img" aria-label="Foto: Team im Gespräch an Arbeitsplätzen in einem offenen Büro"></div>
</section>

<footer class="site-footer">
  <div class="foot-col" style="left:75px"><h3>Home</h3><a>Über KLR</a><a>Kunden</a><a>Mission</a><a>Team</a></div>
  <div class="foot-col" style="left:216px"><h3>Leistungen</h3><a>Industrieanlagenbau</a><a>Reinraumtechnik</a><a>Gasversorgungsanlagen</a><a>Sondermaschinenbau</a><a>Produkte</a><a>Projekt-Management</a><a>Behörden-Management</a></div>
  <div class="foot-col" style="left:440px"><h3>Jobs &amp; Karriere</h3><a>Stellenangebote</a><a>Arbeiten bei KLR</a></div>
  <div class="foot-col" style="left:634px"><h3>Kundenportal</h3><a>Link zu NAS</a></div>
  <div class="foot-brand"><span class="foot-brand-dot"></span>KLR</div>
  <div class="foot-address">
    <p><strong>Standort Bergfeld</strong><br>Lindengasse 14<br>A-5120 Bergfeld<br>Telefon: +43 (0) 555018-0</p>
    <p><strong>Standort Wiesenau</strong><br>Feldweg 52<br>A-2471 Wiesenau<br>Telefon: +43 (0) 555018-0</p>
  </div>
  <div class="legal">
    <span style="left:0">© KLR Services GmbH 2021</span>
    <a style="left:204px;text-decoration:underline">Impressum</a>
    <a style="left:329px;text-decoration:underline">AGB</a>
    <a style="left:411px;text-decoration:underline">Datenschutz</a>
    <a style="left:541px;text-decoration:underline">Nachhaltigkeit</a>
  </div>
</footer>
</body>
</html>
```